Business Card for Multi-Brand Sportswear Company

We are looking for a business card which represents our company and the multiple brands within it.

The company: Fen Athletics (LTD)
The brands: Fen, TavaPuni, ElmStretch, Grit and Rain

Employees using these cards would be representing Fen Athletics, rather than any of the individual brands. You will see a current design within the uploaded files, to give some inspiration. The actual text of the brands is not necessary, but the logos should be on there is some format.

Our creative minds on this are stretched, so we are looking for someone to make this their own, and show us what a good business card should look like.

We may like to get these printed with spot gloss, so keep that in mind with your designs.

www.fenathletics.co.uk

Industry/Entity Type

Business

Contact Information for Business Card

Leo Pemberton-Hale
Operations Manager
(+44) 1632 960 418
Leo@fenathletics.co.uk
www.fenathletics.co.uk

Font styles to use
Sans Serif
Other font styles liked:
• Eurostile

Colors
ffffff

Requirements
Nice to have
• Dark (black) background

```html
<!DOCTYPE html>
<html lang="en">
<head>
<meta charset="utf-8">
<title>Fen Athletics – Business Card</title>
<link rel="stylesheet" href="https://fonts.googleapis.com/css2?family=Open+Sans:wght@400;600;700&display=swap">
<style>
  :root {
    --stage: #e8e5e2;
    --card-top: #f4f3f2;
    --card-red: #ec1c24;
    --ink: #1c1c1c;
    --white: #ffffff;
    --faint: rgba(60, 60, 60, 0.28);
  }
  * { box-sizing: border-box; margin: 0; padding: 0; }
  html, body {
    width: 1200px;
    height: 900px;
    overflow: hidden;
    background: var(--stage);
    font-family: "Open Sans", Arial, sans-serif;
  }
  .canvas { position: relative; width: 1200px; height: 900px; }

  .card {
    position: absolute;
    width: 556px;
    height: 343px;
    overflow: hidden;
    box-shadow: 0 6px 18px rgba(0, 0, 0, 0.12);
  }
  .card--front { left: 238px; top: 62px; }
  .card--back  { left: 460px; top: 518px; width: 559px; }

  .card__top {
    height: 185px;
    background: var(--card-top);
    position: relative;
  }
  .card--back .card__top { height: 187px; }
  .card__band {
    height: calc(100% - 185px);
    background: var(--card-red);
    position: relative;
    color: var(--white);
  }
  .card--back .card__band { height: 156px; }

  .wordmark {
    position: absolute;
    left: 0; right: 0; top: 72px;
    text-align: center;
    font-size: 42px;
    font-weight: 700;
    color: var(--ink);
    letter-spacing: 0.5px;
  }
  .wordmark--faint {
    top: 58px;
    color: var(--faint);
    transform: scaleX(-1);
  }

  .person {
    position: absolute;
    right: 313px;
    top: 57px;
    text-align: right;
    white-space: nowrap;
  }
  .person__name { font-size: 17px; font-weight: 700; line-height: 22px; }
  .person__role { font-size: 14px; font-weight: 400; line-height: 22px; }

  .contact {
    position: absolute;
    left: 272px;
    top: 27px;
    font-size: 14px;
    line-height: 20px;
    white-space: nowrap;
  }
  .contact__row { display: flex; align-items: center; gap: 7px; }
  .contact__icon { width: 11px; height: 11px; flex: none; }
  .contact__address { margin-top: 13px; }

  .brands {
    position: absolute;
    inset: 0;
    display: flex;
    align-items: center;
    justify-content: center;
    gap: 26px;
    font-size: 15px;
    font-weight: 600;
  }
</style>
</head>
<body>
<main class="canvas">

  <section class="card card--front" aria-label="Business card front">
    <div class="card__top">
      <div class="wordmark">Fen Athletics</div>
    </div>
    <div class="card__band">
      <div class="person">
        <p class="person__name">Leo Pemberton-Hale</p>
        <p class="person__role">Operations Manager</p>
      </div>
      <div class="contact">
        <p class="contact__row">
          <svg class="contact__icon" viewBox="0 0 12 12" aria-hidden="true">
            <path fill="#fff" d="M1 4c0-1.6 2.2-2.6 5-2.6S11 2.4 11 4v1H8.6V3.8H3.4V5H1zM2.6 6.2l1.6-2h3.6l1.6 2V10H2.6z"/>
          </svg>(+44) 1632 960 418</p>
        <p class="contact__row">
          <svg class="contact__icon" viewBox="0 0 12 12" aria-hidden="true">
            <rect x="1" y="2.5" width="10" height="7" fill="#fff"/>
            <path d="M1.3 3l4.7 3.6L10.7 3" fill="none" stroke="#ec1c24" stroke-width="1"/>
          </svg>Leo@fenathletics.co.uk</p>
        <p class="contact__row">
          <svg class="contact__icon" viewBox="0 0 12 12" aria-hidden="true">
            <circle cx="6" cy="6" r="5.2" fill="#fff"/>
            <path d="M6 1v10M1 6h10M2.4 3.5h7.2M2.4 8.5h7.2" stroke="#ec1c24" stroke-width="0.8" fill="none"/>
          </svg>www.fenathletics.co.uk</p>
        <p class="contact__address">Kiln Yard,Eastholm,<br>Marlow,YO9 4QT</p>
      </div>
    </div>
  </section>

  <section class="card card--back" aria-label="Business card back">
    <div class="card__top">
      <div class="wordmark wordmark--faint">Fen Athletics</div>
    </div>
    <div class="card__band">
      <div class="brands">
        <span class="brands__item">Grit and Rain</span>
        <span class="brands__item">TavaPuni</span>
        <span class="brands__item">ElmStretch</span>
        <span class="brands__item">Fen</span>
      </div>
    </div>
  </section>

</main>
</body>
</html>
```